Business card design Needed for new logo / Construction business, home extensions and new builds

We need a business card design using our new logo files which i will attach to this project :)

We are a small construction business specialising in home extensions, new builds and property development. We are very ambitious and would appreciate professional and elegant designs for our new business card.

Very serious about using the services on MakerQuarry and recently acquired our new logo from here :)

Please get involved, i will feedback when i can as i am very busy but can respond daily, thanks

Target Market(s)

People that want to build onto their houses, new building developments or adding too their existing property

Industry/Entity Type

Construction

Contact Information for Business Card

Renwick Tolliver Construction, Lionel Ashby (Managing Director), Tel 07822254961, email - info@renwick-tolliver, www.renwick-tolliver.co.uk

Colors

Designer to choose colors to be used in the design.

Requirements
Must have
• I like a deep grey on the back please. A lot of you have provided black from and back, try mixing things up a little. The black looks cool 😎 Thanks

```html
<!DOCTYPE html>
<html lang="en">
<head>
<meta charset="utf-8">
<title>Renwick Tolliver Construction – Business Card</title>
<link rel="stylesheet" href="https://fonts.googleapis.com/css2?family=Montserrat:wght@500;700&family=Open+Sans:wght@400&display=swap">
<style>
  :root {
    --backdrop: #3b3b3b;
    --card: #161616;
    --back-grey: #2a2a2a;
    --back-grey-light: #343434;
    --back-grey-deep: #222222;
    --gold: #d9a02c;
    --gold-edge: #c8922a;
    --silver: #d4d4d4;
  }
  * { margin: 0; padding: 0; box-sizing: border-box; }
  html, body { width: 1200px; height: 801px; overflow: hidden; }
  body {
    background: var(--backdrop);
    position: relative;
    font-family: "Open Sans", sans-serif;
  }
  .card {
    position: absolute;
    top: 257px;
    width: 500px;
    height: 286px;
    border: 1px solid var(--gold-edge);
    box-shadow: 0 18px 40px rgba(0,0,0,0.5);
    overflow: hidden;
  }
  .card--front { left: 60px; background: var(--card); }
  .card--back { left: 640px; background: var(--back-grey); }

  /* Front */
  .holder {
    position: absolute;
    right: 34px;
    top: 40px;
    text-align: right;
  }
  .holder__name {
    font-family: "Montserrat", sans-serif;
    font-weight: 700;
    font-size: 21px;
    letter-spacing: 0.5px;
    color: var(--gold);
    text-transform: uppercase;
    line-height: 1.2;
  }
  .holder__role {
    font-size: 13px;
    color: var(--silver);
    margin-top: 2px;
  }
  .rule {
    position: absolute;
    height: 1px;
    background: var(--gold);
  }
  .rule--name { left: 210px; right: 28px; top: 100px; }
  .rule--contact { left: 28px; right: 210px; top: 206px; }

  .brand {
    position: absolute;
    left: 28px;
    top: 150px;
    display: flex;
    align-items: center;
    gap: 9px;
  }
  .brand__mark {
    width: 12px;
    height: 12px;
    background: var(--gold);
    flex: none;
  }
  .brand__name {
    font-family: "Montserrat", sans-serif;
    font-weight: 500;
    font-size: 13px;
    letter-spacing: 1.5px;
    color: var(--silver);
    text-transform: uppercase;
    line-height: 1.35;
  }

  .contact {
    position: absolute;
    left: 28px;
    top: 214px;
    list-style: none;
  }
  .contact__item {
    display: flex;
    align-items: center;
    gap: 10px;
    font-size: 13px;
    color: var(--silver);
    line-height: 21px;
  }
  .contact__icon { width: 12px; height: 12px; flex: none; }

  /* Back */
  .back-field {
    position: absolute;
    inset: 0;
    background: linear-gradient(135deg, var(--back-grey-deep) 0%, var(--back-grey) 50%, var(--back-grey-light) 100%);
  }
  .back-brand {
    position: absolute;
    left: 62%;
    top: 50%;
    transform: translate(-50%, -50%);
    display: flex;
    align-items: center;
    gap: 9px;
  }
  .back-brand .brand__name { color: var(--gold); font-size: 14px; }
</style>
</head>
<body>

  <section class="card card--front" aria-label="Business card front">
    <div class="holder">
      <p class="holder__name">Lionel Ashby</p>
      <p class="holder__role">Managing Director</p>
    </div>
    <div class="rule rule--name"></div>

    <div class="brand">
      <span class="brand__mark"></span>
      <p class="brand__name">Renwick Tolliver<br>Construction</p>
    </div>

    <div class="rule rule--contact"></div>
    <ul class="contact">
      <li class="contact__item">
        <svg class="contact__icon" viewBox="0 0 12 12"><path d="M2.5 1 L4.5 1 L5.3 3.4 L4 4.4 Q5 6.8 7.6 8 L8.6 6.7 L11 7.5 L11 9.5 Q10.5 11 9 11 Q1 10 1 2.8 Q1 1.2 2.5 1Z" fill="var(--gold)"/></svg>
        07822254961
      </li>
      <li class="contact__item">
        <svg class="contact__icon" viewBox="0 0 12 12"><rect x="0.5" y="2" width="11" height="8" rx="1" fill="var(--gold)"/><path d="M1 2.6 L6 6.6 L11 2.6" stroke="var(--card)" stroke-width="1" fill="none"/></svg>
        info@renwick-tolliver
      </li>
      <li class="contact__item">
        <svg class="contact__icon" viewBox="0 0 12 12"><circle cx="6" cy="6" r="5.2" fill="var(--gold)"/><path d="M1 6 H11 M6 1 Q3 6 6 11 M6 1 Q9 6 6 11" stroke="var(--card)" stroke-width="0.8" fill="none"/></svg>
        www.renwick-tolliver.co.uk
      </li>
    </ul>
  </section>

  <section class="card card--back" aria-label="Business card back">
    <div class="back-field" role="img" aria-label="Repeating tone-on-tone gloss pattern of the company mark on deep grey"></div>
    <div class="back-brand">
      <span class="brand__mark"></span>
      <p class="brand__name">Renwick Tolliver</p>
    </div>
  </section>

</body>
</html>
```